Brand new letterhead, business card, email signature etc.

We are a financial company in London, UK. Our website is www.marlowvane.com. We're wanting a complete remodel of the company colours, letter head, business cards, email signatures, etc. Looking to keep the same font for the company name. I have upload a colour palette that we want to work with. We're looking for company letterhead for outgoing letters/ correspondence, letterhead for internal documentation, email signatures, e-letters. etc. Ultimately we will redesign the entire website also. It is important that our clients get a strong, secure, warm, trustworthy, solid feeling and first impression.
Updates

Designs look the same

Target Market(s)

Institutional investors, (ultra) high net worth individuals

Industry/Entity Type

Finance, Invesments banking.

Font styles to use
Other font styles liked:
• Current font is "Champagne & Limousines"

Requirements
Must have
• Must use the colours provided on the PDF uploaded to the portal. The purple = main colour. The red = accent colour.
Nice to have
• Nice to use same font as now for the company name "Corvane". Font is "Champagne & Limousines". Nice to have some reference to the old logo flower, but only subtle.
Should not have
• Do not use the colour red from our website. Use the colours provided on the colour palette PDF that I uploaded in the portal.

```html
<!DOCTYPE html>
<html lang="en">
<head>
<meta charset="utf-8">
<title>Corvane Letterhead</title>
<link href="https://fonts.googleapis.com/css2?family=Josefin+Sans:wght@300;400&family=Open+Sans:wght@400;700&family=Raleway:wght@700&display=swap" rel="stylesheet">
<style>
  :root {
    --backdrop: #c6c7c9;
    --accent-red: #e03616;
    --plum: #2e0219;
    --sand: #dfd9ce;
    --ink-column: #1f1e20;
    --paper: #ffffff;
    --heading: #333333;
    --meta: #7a7a7a;
    --body: #8a8a8a;
    --contact: #2a2a2a;
  }
  * { margin: 0; padding: 0; box-sizing: border-box; }
  html, body { width: 869px; height: 1200px; overflow: hidden; }
  body { background: var(--backdrop); position: relative; font-family: "Open Sans", sans-serif; }

  .palette-label {
    position: absolute; left: 34px; top: 41px;
    font-family: "Josefin Sans", sans-serif; font-weight: 300;
    font-size: 10px; color: #333;
  }
  .swatch {
    position: absolute; top: 56px; height: 16px;
    font-family: "Open Sans", sans-serif; font-weight: 700;
    font-size: 4.5px; line-height: 16px; padding: 4px 0 0 5px; line-height: 10px;
  }
  .swatch--red { left: 34px; width: 74px; background: var(--accent-red); color: #fff; }
  .swatch--plum { left: 115px; width: 74px; background: var(--plum); color: #fff; }
  .swatch--sand { left: 196px; width: 72px; background: var(--sand); color: #222; }

  .letterhead {
    position: absolute; left: 34px; top: 82px; width: 801px; height: 1085px;
    background: var(--paper);
    box-shadow: 2px 3px 6px rgba(0,0,0,0.35);
  }
  .top-band { position: absolute; left: 0; top: 0; width: 100%; height: 33px; background: var(--accent-red); }
  .contact-column { position: absolute; left: 708px; top: 0; width: 40px; height: 216px; background: var(--ink-column); }
  .contact-icon { position: absolute; left: 718px; width: 20px; height: 20px; }
  .contact-icon--phone { top: 94px; }
  .contact-icon--web { top: 142px; }
  .contact-icon--pin { top: 190px; }
  .contact-rule { position: absolute; left: 527px; width: 221px; height: 1.5px; background: var(--sand); }
  .contact-rule--one { top: 129px; }
  .contact-rule--two { top: 173px; }

  .contact-block {
    position: absolute; right: 102px; text-align: right;
    font-family: "Josefin Sans", sans-serif; font-weight: 300;
    font-size: 11.5px; line-height: 14px; color: var(--contact);
  }
  .contact-block--phone { top: 89px; }
  .contact-block--web { top: 138px; }
  .contact-block--address { top: 184px; }

  .brand { position: absolute; left: 87px; top: 90px; display: flex; align-items: center; }
  .brand-square { width: 51px; height: 51px; border: 1px solid #222; }
  .brand-name {
    margin-left: 12px;
    font-family: "Josefin Sans", sans-serif; font-weight: 300;
    font-size: 29px; letter-spacing: 6px; color: #222; line-height: 1; padding-top: 6px;
  }

  .recipient { position: absolute; left: 90px; top: 258px; }
  .recipient-name { font-size: 18px; font-weight: 700; color: var(--heading); line-height: 24px; }
  .recipient-details { margin-top: 6px; font-size: 12.5px; line-height: 17.6px; color: var(--meta); }

  .letter-body { position: absolute; left: 90px; top: 398px; width: 624px; }
  .letter-body p {
    font-size: 12.5px; line-height: 17.5px; color: var(--body);
    text-align: justify; margin-bottom: 17.5px;
  }

  .signature-mark {
    position: absolute; left: 90px; top: 848px; width: 152px; height: 30px;
    background: linear-gradient(90deg, #e9e9e9, #d4d4d4);
  }
  .signatory { position: absolute; left: 90px; top: 882px; }
  .signatory-name { font-family: "Raleway", sans-serif; font-weight: 700; font-size: 16px; color: var(--heading); line-height: 22px; }
  .signatory-role { font-size: 12.5px; color: var(--meta); line-height: 20px; }
</style>
</head>
<body>
  <div class="palette-label">used colors given by client</div>
  <div class="swatch swatch--red">E03616</div>
  <div class="swatch swatch--plum">2E0219</div>
  <div class="swatch swatch--sand">DFD9CE</div>

  <main class="letterhead">
    <div class="top-band"></div>
    <div class="contact-column"></div>

    <svg class="contact-icon contact-icon--phone" viewBox="0 0 20 20" aria-hidden="true">
      <path d="M2 7 Q10 1 18 7 L16 9 L13 8 L13 6 Q10 5 7 6 L7 8 L4 9 Z" fill="#fff"/>
      <path d="M5 10 L15 10 L17 16 L3 16 Z" fill="#fff"/>
      <g fill="#1f1e20"><rect x="8" y="11.5" width="1" height="1"/><rect x="10" y="11.5" width="1" height="1"/><rect x="12" y="11.5" width="1" height="1"/><rect x="8" y="13.5" width="1" height="1"/><rect x="10" y="13.5" width="1" height="1"/><rect x="12" y="13.5" width="1" height="1"/></g>
    </svg>
    <svg class="contact-icon contact-icon--web" viewBox="0 0 20 20" aria-hidden="true">
      <circle cx="10" cy="10" r="7.5" fill="none" stroke="#fff" stroke-width="1.8"/>
      <path d="M4 7 Q10 10 16 13 M7 3.5 Q9 10 13 16.5 M3.5 12 Q8 8 14 4" fill="none" stroke="#fff" stroke-width="1.4"/>
    </svg>
    <svg class="contact-icon contact-icon--pin" viewBox="0 0 20 20" aria-hidden="true">
      <path d="M10 1 C5.5 1 3.5 4.5 3.5 7.5 C3.5 12 10 19 10 19 C10 19 16.5 12 16.5 7.5 C16.5 4.5 14.5 1 10 1 Z" fill="#fff"/>
      <circle cx="10" cy="7.5" r="2.3" fill="#1f1e20"/>
    </svg>

    <div class="contact-rule contact-rule--one"></div>
    <div class="contact-rule contact-rule--two"></div>

    <div class="contact-block contact-block--phone">+000 12345 6789<br>+000 12345 6789</div>
    <div class="contact-block contact-block--web">urwebsitename.com<br>urname@email.com</div>
    <div class="contact-block contact-block--address">1234 Street name, town/city,<br>state/country, post/zip, 012345.</div>

    <div class="brand">
      <div class="brand-square"></div>
      <div class="brand-name">CORVANE</div>
    </div>

    <section class="recipient">
      <div class="recipient-name">Name Surname</div>
      <div class="recipient-details">
        Senior Executive<br>
        Address goes here. Street, City, Country<br>
        contact@yourmail.com<br>
        000-987-654-321
      </div>
    </section>

    <section class="letter-body">
      <p>Lorem ipsum dolor sit amet, consectetur adipisicing elit, sed do eiusmod tempor incididunt ut labore et dolore magna aliqua. Ut enim ad minim veniam, quis nostrud exercitation ullamco laboris nisi ut aliquip ex ea commodo consequat. Duis aute irure dolor in reprehenderit in voluptate velit esse cillum dolore eu fugiat nulla pariatur. Excepteur sint occaecat cupidatat non proident, sunt in culpa qui officia deserunt mollit anim id est laborum. Sed ut perspiciatis unde omnis iste natus error sit voluptatem accusantium doloremque laudantium, totam rem aperiam, eaque ipsa quae ab illo inventore veritatis et quasi architecto beatae vitae dicta sunt explicabo. Nemo enim ipsam voluptatem quia voluptas sit aspernatur aut odit aut fugit, sed quia consequuntur magni dolores eos qui ratione voluptatem sequi nesciunt. Neque porro voluptatem sequi nesciunt. Nemo enim ipsam voluptatem quia voluptas.</p>
      <p>Lorem ipsum dolor sit amet, consectetur adipisicing elit, sed do eiusmod tempor incididunt ut labore et dolore magna aliqua. Ut enim ad minim veniam, quis nostrud exercitation ullamco laboris nisi ut aliquip ex ea commodo consequat. Duis aute irure dolor in reprehenderit in voluptate velit esse cillum dolore eu fugiat nulla pariatur. Excepteur sint occaecat cupidatat non proident, sunt in culpa qui officia deserunt mollit anim id est laborum. Sed ut perspiciatis unde omnis iste natus error sit voluptatem accusantium doloremque laudantium, totam rem aperiam, eaque ipsa quae ab illo inventore veritatis et quasi architecto beatae vitae dicta sunt explicabo. Nemo enim ipsam voluptatem quia voluptas sit aspernatur aut odit aut.</p>
      <p>Lorem ipsum dolor sit amet, consectetur adipisicing elit, sed do eiusmod tempor incididunt ut labore et dolore magna aliqua. Ut enim ad minim veniam, quis nostrud exercitation ullamco laboris nisi ut aliquip ex ea commodo consequat. .</p>
    </section>

    <div class="signature-mark" role="img" aria-label="Handwritten signature of the signatory"></div>
    <section class="signatory">
      <div class="signatory-name">NAME SURNAME</div>
      <div class="signatory-role">General Manager</div>
    </section>
  </main>
</body>
</html>
```